Request for Business Card Design

Hi. My name is Marlene, I am looking for a new business card design for my company, Quarrow Signal Instruments, LLC. I really like the design you did for Tarsel Venture and was hoping you could do something similar using our full logo and our mark. I am also open to any raised texture design using our mark. I have attached our full logo, which would need to be somewhere on the card, as well as the mark in both outline and full form, as well as our brand colors / guide. The card does not have to be white, as long as our logo and mark appear. I actually like darker colored business cards more, but am open to all options. If you are interested in working with me, please let me know. We would also take the business card design into letterhead design if you can do that.

```html
<!DOCTYPE html>
<html lang="en">
<head>
<meta charset="utf-8">
<title>Quarrow Signal Instruments — Business Card</title>
<link rel="stylesheet" href="https://fonts.googleapis.com/css2?family=Roboto:wght@400;500;700;900&display=swap">
<style>
  :root {
    --backdrop-light: #d6d6d6;
    --backdrop-dark: #a9a9a9;
    --card-black: #141414;
    --card-edge: #1a9fd0;
    --brand-blue: #1a9fd0;
    --text-white: #f2f2f2;
    --divider: #3a3a3a;
    --pattern-dark: #0e0e0e;
    --pattern-light: #2c2c2c;
  }
  * { box-sizing: border-box; margin: 0; padding: 0; }
  html, body {
    width: 1200px; height: 800px; overflow: hidden;
  }
  body {
    background: linear-gradient(135deg, var(--backdrop-dark), var(--backdrop-light));
    font-family: "Roboto", Arial, sans-serif;
    display: flex; align-items: center; justify-content: center; gap: 40px;
  }
  .card {
    width: 540px; height: 310px;
    background: var(--card-black);
    border-bottom: 3px solid var(--card-edge);
    box-shadow: 0 14px 30px rgba(0,0,0,0.35);
    position: relative;
    overflow: hidden;
  }

  /* Front */
  .card-front { display: flex; }
  .brand-block {
    width: 50%;
    display: flex; flex-direction: column; justify-content: center; align-items: center;
    gap: 8px;
    color: var(--text-white);
    font-weight: 700;
    text-align: center;
  }
  .brand-dot {
    width: 46px; height: 46px; border-radius: 50%;
    background: var(--brand-blue);
    margin-bottom: 10px;
  }
  .brand-name { font-size: 34px; letter-spacing: 3px; line-height: 1; }
  .brand-tagline { font-size: 11px; letter-spacing: 1.6px; }
  .divider {
    width: 1px; margin: 40px 0;
    background: linear-gradient(to bottom, transparent, var(--divider), transparent);
  }
  .contact-block {
    width: 50%;
    padding: 54px 0 0 30px;
    color: var(--text-white);
  }
  .person-name {
    color: var(--brand-blue);
    font-weight: 700; font-size: 21px; letter-spacing: 0.5px;
    text-transform: uppercase;
  }
  .person-role { font-size: 13px; margin-bottom: 20px; }
  .contact-list { list-style: none; font-size: 13px; line-height: 1.6; }
  .contact-list li { display: flex; align-items: center; gap: 8px; }
  .contact-list svg { width: 13px; height: 13px; flex: none; }
  .address { margin-top: 18px; font-size: 13px; line-height: 1.45; }

  /* Back */
  .raised-pattern {
    position: absolute; inset: 0;
    background: radial-gradient(ellipse at 80% 20%, var(--pattern-light), var(--pattern-dark) 70%);
  }
  .back-mark {
    position: absolute; left: 50%; top: 50%;
    transform: translate(-50%, -50%);
    display: flex; align-items: center; gap: 8px;
    color: var(--brand-blue);
    font-weight: 700; font-size: 14px; letter-spacing: 2px;
  }
  .back-dot { width: 22px; height: 22px; border-radius: 50%; background: var(--brand-blue); }
</style>
</head>
<body>

  <section class="card card-front">
    <div class="brand-block">
      <span class="brand-dot"></span>
      <span class="brand-name">QUARROW</span>
      <span class="brand-tagline">SIGNAL INSTRUMENTS</span>
    </div>
    <div class="divider"></div>
    <div class="contact-block">
      <h1 class="person-name">Elias Brandt</h1>
      <p class="person-role">Managing Director</p>
      <ul class="contact-list">
        <li>
          <svg viewBox="0 0 24 24" fill="var(--brand-blue)"><path d="M6.6 10.8a15 15 0 0 0 6.6 6.6l2.2-2.2a1 1 0 0 1 1-.25 11.4 11.4 0 0 0 3.6.57 1 1 0 0 1 1 1V20a1 1 0 0 1-1 1A17 17 0 0 1 3 4a1 1 0 0 1 1-1h3.5a1 1 0 0 1 1 1c0 1.25.2 2.45.57 3.57a1 1 0 0 1-.25 1z"/></svg>
          044-555 019 238
        </li>
        <li>
          <svg viewBox="0 0 24 24" fill="var(--brand-blue)"><path d="M2 5h20v14H2z M2 5l10 8 10-8" stroke="var(--card-black)" stroke-width="1.5"/></svg>
          hello@quarrowsignal.com
        </li>
        <li>
          <svg viewBox="0 0 24 24" fill="none" stroke="var(--brand-blue)" stroke-width="2"><circle cx="12" cy="12" r="9.5"/><path d="M2.5 12h19M12 2.5c3 3 3 16 0 19M12 2.5c-3 3-3 16 0 19"/></svg>
          www.quarrowsignal.com
        </li>
      </ul>
      <p class="address">17, Fenwick Row, Hallbrook<br>30918, Northland</p>
    </div>
  </section>

  <section class="card card-back">
    <div class="raised-pattern" role="img" aria-label="Raised embossed repeat pattern of the company mark on black"></div>
    <div class="back-mark">
      <span class="back-dot"></span>
      <span>QUARROW</span>
    </div>
  </section>

</body>
</html>
```